Mortgage Company ready to make a statement!

We have a basic logo that I am fairly happy with ... but it could use a little bit of tweaking before we order the sign for our building. We also want some knock-your-socks-off business cards.
Problem: Inside of our Mortgage Office (Bright Fern Mortgage Group), we are going to have a coffee lounge (Sunbrew Cafe) for Realtors to use instead of the local Cuppington to meet with homebuyers. The office and coffee lounge are in an industrial building and is decorated with cozy overstuffed chairs, a hodge podge of interesting lamps and furniture, and goal is to make it as inviting as possible. However, we are a financial institution... so we need to keep it pretty clean as well.
One of my favorite marketing ideas is to cut a house key for everyone who buys a home using us with a key that matches our logo. There's only one key shape that works really well, so that needs to match the logo in order for the idea to work. I'll attach an image of the key blank.... although the way the key hole cut out looks terrible, so I was thinking of having them just do a thin outline instead.
Would like a similar, matching logo for the Sunbrew Cafe... but possibly something that would be a little less formal and would be cute on a coffee mug- nothing stuffy.
AND, we're opening a home inspection company as well, and we would like that logo and branding to match. The home inspection company is "Bright Fern Home Inspections"
We were thinking that for the home inspection company , we could use a magnifying glass shape inside of the house shape for the logo, use a keyhole shape inside of the same house for the mortgage company, and use a coffee cup inside of the house shape for Sunbrew Cafe.
Just getting stuck and need to help. I designed the attached logo myself, and that is what we are currently using. Designers at local printing companies have failed to impress us.
The mortgage industry has a lot of numbers and logos, etc that they require us to put on our business cards... so it's hard to keep them looking clean.
HELP! HELP! :)

```html
<!DOCTYPE html>
<html lang="en">
<head>
<meta charset="utf-8">
<title>Bright Fern Mortgage Group – Business Card</title>
<link rel="stylesheet" href="https://fonts.googleapis.com/css2?family=Open+Sans:wght@400;600;700&display=swap">
<style>
  :root {
    --stage: #2b2b2b;
    --card-light: #f3f3f3;
    --brand-teal: #23657f;
    --band-teal: #4e8299;
    --ink-grey: #555a5e;
    --rule-grey: #8a8f93;
    --white: #ffffff;
  }
  * { margin: 0; padding: 0; box-sizing: border-box; }
  html, body {
    width: 1200px; height: 960px; overflow: hidden;
    background: var(--stage);
    font-family: "Open Sans", Arial, sans-serif;
  }
  .stage { position: relative; width: 1200px; height: 960px; }

  .card { position: absolute; width: 600px; height: 343px; }
  .card-front { left: 314px; top: 113px; background: var(--card-light); }
  .card-back { left: 311px; top: 472px; background: var(--brand-teal); }

  .brand { position: absolute; display: flex; align-items: center; gap: 14px; font-weight: 400; }
  .brand-mark { flex: none; }
  .brand-name { line-height: 1; }
  .brand-name .line-main { display: block; letter-spacing: 0.5px; }
  .brand-name .line-sub { display: block; margin-top: 6px; }

  .card-front .brand { left: 44px; top: 54px; color: var(--brand-teal); }
  .card-front .brand-mark { width: 36px; height: 36px; background: var(--brand-teal); }
  .card-front .line-main { font-size: 40px; }
  .card-front .line-sub { font-size: 23px; }

  .card-back .brand { left: 50%; top: 50%; transform: translate(-50%, -50%); color: var(--white); }
  .card-back .brand-mark { width: 24px; height: 24px; background: var(--white); }
  .card-back .line-main { font-size: 30px; }
  .card-back .line-sub { font-size: 17px; margin-top: 4px; }

  .holder { position: absolute; left: 37px; top: 210px; color: var(--ink-grey); }
  .holder-name { font-size: 20px; font-weight: 700; color: var(--brand-teal); letter-spacing: 0.3px; }
  .holder-title { font-size: 15px; margin-top: 2px; }
  .holder-address { font-size: 14px; line-height: 17px; margin-top: 14px; }

  .contact { position: absolute; left: 306px; top: 215px; color: var(--ink-grey); font-size: 13.5px; }
  .licence { margin-bottom: 12px; }
  .contact-list { list-style: none; }
  .contact-list li { display: flex; align-items: center; gap: 8px; height: 19px; }
  .contact-list svg { width: 13px; height: 13px; fill: var(--brand-teal); flex: none; }

  .footer-rule { position: absolute; left: 0; right: 0; top: 330px; height: 1px; background: var(--rule-grey); }
  .footer-band { position: absolute; left: 0; right: 0; bottom: 0; height: 9px; background: var(--band-teal); }
</style>
</head>
<body>
<main class="stage">

  <section class="card card-front" aria-label="Business card front">
    <div class="brand">
      <span class="brand-mark"></span>
      <span class="brand-name">
        <span class="line-main">BRIGHT FERN</span>
        <span class="line-sub">Mortgage Group</span>
      </span>
    </div>

    <div class="holder">
      <p class="holder-name">DANA WHITLOW</p>
      <p class="holder-title">Branch Manager</p>
      <p class="holder-address">Bright Fern Mortgage Group<br>18 N. Alder Street, Suite 210<br>Millbrook, CO 80000</p>
    </div>

    <div class="contact">
      <p class="licence">NMLS# 1048207</p>
      <ul class="contact-list">
        <li>
          <svg viewBox="0 0 16 16" aria-hidden="true"><path d="M3.6 1.2 6 3.6 4.8 5.6c.9 2 2.6 3.7 4.6 4.6l2-1.2 2.4 2.4-1.6 2.6C7 13.6 2.4 9 1 3.2z"/></svg>
          <span>555-014-2303</span>
        </li>
        <li>
          <svg viewBox="0 0 16 16" aria-hidden="true"><path d="M4.5 0h7A1.5 1.5 0 0 1 13 1.5v13a1.5 1.5 0 0 1-1.5 1.5h-7A1.5 1.5 0 0 1 3 14.5v-13A1.5 1.5 0 0 1 4.5 0zM5 2v10h6V2zm3 11a1 1 0 1 0 0 2 1 1 0 0 0 0-2z"/></svg>
          <span>555-014-2370</span>
        </li>
        <li>
          <svg viewBox="0 0 16 16" aria-hidden="true"><path d="M1 3h14v1.2L8 8.6 1 4.2zm0 2.6 7 4.4 7-4.4V13H1z"/></svg>
          <span>Dana@BrightFernLoans.com</span>
        </li>
        <li>
          <svg viewBox="0 0 16 16" aria-hidden="true"><circle cx="8" cy="8" r="7"/><path d="M4 6c2-1 3 1 4 0s2-2 3-1c-1 2 1 3 0 5-2 1-2-1-4 1-1-2-2-2-3-5z" fill="#f3f3f3"/></svg>
          <span>www.BrightFernLoans.com</span>
        </li>
      </ul>
    </div>

    <div class="footer-rule"></div>
    <div class="footer-band"></div>
  </section>

  <section class="card card-back" aria-label="Business card back">
    <div class="brand">
      <span class="brand-mark"></span>
      <span class="brand-name">
        <span class="line-main">BRIGHT FERN</span>
        <span class="line-sub">Mortgage Group</span>
      </span>
    </div>
  </section>

</main>
</body>
</html>
```